Professional Photography Business cards

I need business cards that include my logo which I have uploaded. I run a photography business. I am open to ideas but I would like one side to have my logo and the other side to have my contact info. I don't have a website made but I do own a website domain. I have uploaded 2 different logo color schemes. My business colors are Blue, black , and white.

Business Name
Business Phone Number
Business Email
Business Website address
Instagram

Industry/Entity Type

Professional Photography

Contact Information for Business Card

Phone Number: 916-384-7702 email: info@tlane-studio.example Instagram: @t.lanestudio website doman- www.tlane-studio.example

Requirements
Must have
• I like the idea of a business card with a full black background front and back of card. My colors must include royal blue, black, and white

```html
<!DOCTYPE html>
<html lang="en">
<head>
<meta charset="utf-8">
<title>T. Lane Studio — Business Cards</title>
<link rel="stylesheet" href="https://fonts.googleapis.com/css2?family=Open+Sans:wght@400;600&display=swap">
<style>
  :root {
    --backdrop: #2a2a2c;
    --card-black: #141415;
    --royal-blue: #2b2fa0;
    --accent-blue: #3a3fc4;
    --ink-white: #ffffff;
    --emboss-grey: #6d6d72;
  }
  * { box-sizing: border-box; margin: 0; padding: 0; }
  html, body {
    width: 1200px; height: 900px; overflow: hidden;
    background: var(--backdrop);
    font-family: "Open Sans", sans-serif;
  }
  .sheet {
    width: 1200px; height: 900px;
    display: flex; flex-direction: column;
    align-items: center; justify-content: center; gap: 44px;
  }
  .card {
    position: relative;
    width: 700px; height: 400px;
    background: var(--card-black);
    border-bottom: 7px solid var(--royal-blue);
    box-shadow: 0 14px 30px rgba(0,0,0,.45);
  }
  /* contact side */
  .card--contact { display: flex; align-items: center; padding: 0 56px; }
  .brand { display: flex; align-items: center; gap: 14px; width: 290px; }
  .brand__dot {
    width: 22px; height: 22px; border-radius: 50%;
    border: 3px solid var(--ink-white); flex: none;
  }
  .brand__name {
    font-weight: 600; font-size: 30px; letter-spacing: .5px;
    color: var(--ink-white);
  }
  .divider {
    width: 1px; height: 150px; background: var(--accent-blue);
    margin: 0 30px 0 10px;
  }
  .contact-list { list-style: none; display: flex; flex-direction: column; gap: 12px; }
  .contact-list li {
    display: flex; align-items: center; gap: 12px;
    color: var(--ink-white); font-size: 19px;
  }
  .contact-list svg { width: 18px; height: 18px; flex: none; }
  /* logo side */
  .card--logo { display: flex; align-items: center; justify-content: center; }
  .card--logo .brand { width: auto; gap: 22px; }
  .card--logo .brand__dot { width: 44px; height: 44px; border: 5px solid var(--emboss-grey); }
  .card--logo .brand__name { font-size: 48px; color: var(--emboss-grey); }
</style>
</head>
<body>
<main class="sheet">
  <section class="card card--contact" aria-label="Card front with contact details">
    <div class="brand">
      <span class="brand__dot"></span>
      <span class="brand__name">T. Lane Studio</span>
    </div>
    <div class="divider"></div>
    <ul class="contact-list">
      <li>
        <svg viewBox="0 0 24 24" aria-hidden="true"><path fill="#3a3fc4" d="M6.6 10.8a15 15 0 0 0 6.6 6.6l2.2-2.2a1 1 0 0 1 1-.25 11.4 11.4 0 0 0 3.6.57 1 1 0 0 1 1 1V20a1 1 0 0 1-1 1A17 17 0 0 1 3 4a1 1 0 0 1 1-1h3.5a1 1 0 0 1 1 1c0 1.25.2 2.45.57 3.6a1 1 0 0 1-.25 1z"/></svg>
        916-384-7702
      </li>
      <li>
        <svg viewBox="0 0 24 24" aria-hidden="true"><rect x="2" y="5" width="20" height="14" rx="1.5" fill="#3a3fc4"/><path d="M3 6l9 7 9-7" stroke="#141415" stroke-width="1.8" fill="none"/></svg>
        info@tlane-studio.example
      </li>
      <li>
        <svg viewBox="0 0 24 24" aria-hidden="true"><circle cx="12" cy="12" r="9" fill="none" stroke="#3a3fc4" stroke-width="2"/><path d="M3 12h18M12 3c3 3 3 15 0 18M12 3c-3 3-3 15 0 18" stroke="#3a3fc4" stroke-width="1.6" fill="none"/></svg>
        www.tlane-studio.example
      </li>
      <li>
        <svg viewBox="0 0 24 24" aria-hidden="true"><rect x="4" y="4" width="16" height="16" rx="2" fill="none" stroke="#3a3fc4" stroke-width="2"/></svg>
        @t.lanestudio
      </li>
    </ul>
  </section>

  <section class="card card--logo" aria-label="Card back with studio name">
    <div class="brand">
      <span class="brand__dot"></span>
      <span class="brand__name">T. Lane Studio</span>
    </div>
  </section>
</main>
</body>
</html>
```